Business Card For Halvenmoor Financial Consulting

Hi, I would like a business card designed. Bold, modern.
Please use the same design as the logo. I have also attached the website design to see the overall theme.
Wordmark Font
Color: Hex: #01AEF7

```html
<!DOCTYPE html>
<html lang="en">
<head>
<meta charset="utf-8">
<title>Halvenmoor Financial Consulting – Business Card</title>
<link href="https://fonts.googleapis.com/css2?family=Montserrat:wght@700&family=Roboto:wght@400;500&display=swap" rel="stylesheet">
<style>
  :root {
    --stage: #2b2c2e;
    --navy-deep: #0f1a26;
    --navy: #1c2b3b;
    --brand-blue: #01aef7;
    --blue-dark: #1a8ff0;
    --white: #ffffff;
    --white-soft: rgba(255,255,255,0.9);
  }
  * { margin: 0; padding: 0; box-sizing: border-box; }
  html, body {
    width: 1200px; height: 939px; overflow: hidden;
    background: var(--stage);
  }
  .stage { position: relative; width: 1200px; height: 939px; }
  .card {
    position: absolute; width: 540px; height: 308px;
    overflow: hidden; box-shadow: 0 14px 30px rgba(0,0,0,0.45);
  }
  .card--front { left: 70px; top: 110px; }
  .card--back { left: 590px; top: 520px; }

  .front-backdrop {
    position: absolute; inset: 0;
    background: radial-gradient(ellipse at 55% 45%, var(--navy) 0%, var(--navy-deep) 75%);
  }
  .back-backdrop {
    position: absolute; inset: 0;
    background: linear-gradient(160deg, var(--brand-blue) 0%, var(--blue-dark) 100%);
  }

  .brand {
    position: absolute; display: flex; align-items: center; gap: 12px;
  }
  .brand-square {
    width: 34px; height: 34px; border: 4px solid var(--brand-blue); flex: none;
  }
  .card--back .brand-square { border-color: var(--white); width: 30px; height: 30px; }
  .brand-name {
    font-family: "Montserrat", sans-serif; font-weight: 700;
    color: var(--white); text-transform: uppercase; line-height: 1.1;
    white-space: nowrap;
  }
  .card--front .brand { left: 50%; top: 50%; transform: translate(-50%, -50%); }
  .card--front .brand-name { font-size: 24px; letter-spacing: 1.5px; }
  .card--back .brand { left: 30px; top: 128px; gap: 10px; }
  .card--back .brand-name { font-size: 15px; letter-spacing: 1px; }

  .divider {
    position: absolute; left: 250px; top: 40px; width: 1px; height: 228px;
    background: var(--white-soft);
  }
  .contact {
    position: absolute; left: 272px; top: 52px; color: var(--white);
    font-family: "Roboto", sans-serif;
  }
  .contact-name {
    font-family: "Montserrat", sans-serif; font-weight: 700;
    font-size: 20px; letter-spacing: 0.5px; text-transform: uppercase;
  }
  .contact-role { font-size: 12px; margin-top: 2px; }
  .contact-address { font-size: 12px; line-height: 1.45; margin-top: 12px; }
  .contact-list { list-style: none; margin-top: 12px; font-size: 12px; }
  .contact-list li { display: flex; align-items: center; gap: 8px; height: 20px; }
  .contact-list svg { width: 12px; height: 12px; flex: none; }
</style>
</head>
<body>
<main class="stage">
  <section class="card card--front" aria-label="Business card front">
    <div class="front-backdrop" role="img" aria-label="Dark blurred financial chart background with line graphs and bars"></div>
    <div class="brand">
      <span class="brand-square"></span>
      <span class="brand-name">Halvenmoor<br>Financial Consulting</span>
    </div>
  </section>

  <section class="card card--back" aria-label="Business card back">
    <div class="back-backdrop" role="img" aria-label="Faint blue stock chart with bars and line graph"></div>
    <div class="brand">
      <span class="brand-square"></span>
      <span class="brand-name">Halvenmoor<br>Financial<br>Consulting</span>
    </div>
    <div class="divider"></div>
    <div class="contact">
      <p class="contact-name">Marco Ellison</p>
      <p class="contact-role">Credit Funding Consultant</p>
      <p class="contact-address">418 Corwin Ave. Suite 300<br>Ashfield, NJ 07120</p>
      <ul class="contact-list">
        <li>
          <svg viewBox="0 0 12 12" aria-hidden="true"><rect x="3" y="0.5" width="6" height="11" rx="1" fill="none" stroke="#fff"/><circle cx="6" cy="9.5" r="0.7" fill="#fff"/></svg>
          (555) 214 3800
        </li>
        <li>
          <svg viewBox="0 0 12 12" aria-hidden="true"><path d="M2.5 1 L4.5 1 L5.3 3.6 L4 4.6 Q5 7 7.4 8 L8.4 6.7 L11 7.5 L11 9.5 Q10.5 11 9 11 Q1 10 1 2.5 Q1 1 2.5 1 Z" fill="#fff"/></svg>
          (555) 610-0247
        </li>
        <li>
          <svg viewBox="0 0 12 12" aria-hidden="true"><rect x="0.5" y="2" width="11" height="8" fill="#fff"/><path d="M0.5 2 L6 6.5 L11.5 2" fill="none" stroke="#1a8ff0"/></svg>
          info@halvenmoorconsulting.com
        </li>
        <li>
          <svg viewBox="0 0 12 12" aria-hidden="true"><circle cx="6" cy="6" r="5.2" fill="none" stroke="#fff"/><ellipse cx="6" cy="6" rx="2.2" ry="5.2" fill="none" stroke="#fff"/><path d="M1 6 H11" stroke="#fff"/></svg>
          halvenmoorconsulting.com
        </li>
      </ul>
    </div>
  </section>
</main>
</body>
</html>
```